World travel poster - I want to remember where I've been!

I would like a poster for me to print and keep in my home as a record of my world travels. It must look like a mechanical sign in an airport (see picture for example) However I am flexible with exact layout, if you'd like to add images used to enhance poster etc. I have also uploaded some pictures from my travels if you would like to use some or all of them. They are named according to location.

Poster must include:
USA 2003
Malaysia 2006
Thailand 2007
Italy 2009
India, Vietnam, Hong Kong 2010
Bali 2011
Malaysia 2012
Singapore 2012
Vietnam, Cambodia, Laos 2013
Europe 2015

and the quote:

"The world is a book and those who do not travel read only one page."
― Severin of Caldra
Updates

Hi there. I have uploaded some photos of my travels to possibly use in my poster. They are named according to location. I haven't decided if I prefer the originial layout or with images, so please post both for me to consider. Thanks so much for your time to consider my project.

Target Market(s)

Something to catch the eye of visitors and remind me of my adventures.
A classic piece that is a conversation starter.

Industry/Entity Type

Airport

Font styles to use
Other font styles liked:
• Airport mechanical font

Requirements
Must have
• Some lettering like a mechanical airport board (see image attached for example).
Dimensions that are easy to print - either A3, or a long/narrow poster.
Nice to have
• A splash of colour or an image, maybe the words 'arrivals' or 'departures'

Use of some of my pictures if it doesn't look too busy.
Should not have
• Anything too over the top.

```html
<!DOCTYPE html>
<html lang="en">
<head>
<meta charset="utf-8">
<title>Departures – Travel Record Poster</title>
<link rel="stylesheet" href="https://fonts.googleapis.com/css2?family=Montserrat:wght@300;600;700&family=Oswald:wght@500&display=swap">
<style>
  :root {
    --bg: #2c2c2c;
    --accent: #f6d100;
    --tile-top: #3a3a3a;
    --tile-bottom: #1c1c1c;
    --tile-edge: #0e0e0e;
    --flap-text: #f2f2f2;
    --quote-text: #d9d9d9;
  }
  * { margin: 0; padding: 0; box-sizing: border-box; }
  html, body { width: 837px; height: 1200px; overflow: hidden; background: var(--bg); }
  .poster {
    position: relative;
    width: 837px; height: 1200px;
    background: var(--bg);
  }
  .board-title {
    position: absolute; left: 34px; top: 34px;
    display: flex; align-items: center; gap: 26px;
    color: var(--accent);
    font-family: "Montserrat", sans-serif; font-weight: 600;
    font-size: 33px; letter-spacing: 0.13em;
  }
  .board-title svg { width: 58px; height: 30px; }
  .board {
    position: absolute; left: 34px; top: 121px;
    display: flex; flex-direction: column; gap: 16px;
  }
  .row { display: flex; align-items: center; height: 44px; }
  .tile {
    position: relative;
    width: 38px; height: 44px; margin-right: 6px;
    background: linear-gradient(to bottom, var(--tile-top) 0%, #2a2a2a 49%, var(--tile-edge) 50%, #262626 52%, var(--tile-bottom) 100%);
    border-radius: 2px;
    box-shadow: 0 1px 0 rgba(0,0,0,.6), inset 0 0 0 1px rgba(255,255,255,.04);
    color: var(--flap-text);
    font-family: "Oswald", sans-serif; font-weight: 500;
    font-size: 31px; line-height: 44px; text-align: center;
  }
  .tile.accent { color: var(--accent); }
  .flag {
    display: block; width: 84px; height: 44px; margin-left: 4px; margin-right: 14px;
    box-shadow: 0 1px 0 rgba(0,0,0,.5);
  }
  .quote {
    position: absolute; left: 34px; top: 995px; width: 780px;
    font-family: "Montserrat", sans-serif; font-weight: 300;
    font-size: 45px; line-height: 57px; color: var(--quote-text);
  }
  .quote strong { font-weight: 700; color: var(--accent); }
</style>
</head>
<body>
<main class="poster">
  <header class="board-title">
    <svg viewBox="0 0 58 30" aria-hidden="true"><path fill="currentColor" d="M2 17 L8 17 L13 22 L22 22 L16 30 L22 30 L34 22 L52 22 C57 22 58 18 54 17 L34 15 L22 2 L16 2 L22 15 L12 15 L7 11 L2 11 Z"/></svg>
    <h1 style="font:inherit">DEPARTURES</h1>
  </header>

  <section class="board">
    <div class="row"><span class="tile">U</span><span class="tile">S</span><span class="tile">A</span><span class="tile">-</span><span class="tile">2</span><span class="tile">0</span><span class="tile">0</span><span class="tile">3</span>
      <svg class="flag" viewBox="0 0 19 10" preserveAspectRatio="none" role="img" aria-label="USA flag"><rect width="19" height="10" fill="#fff"/><g fill="#b22234"><rect y="0" width="19" height=".77"/><rect y="1.54" width="19" height=".77"/><rect y="3.08" width="19" height=".77"/><rect y="4.62" width="19" height=".77"/><rect y="6.15" width="19" height=".77"/><rect y="7.69" width="19" height=".77"/><rect y="9.23" width="19" height=".77"/></g><rect width="7.6" height="5.38" fill="#3c3b6e"/></svg></div>

    <div class="row"><span class="tile">M</span><span class="tile">A</span><span class="tile">L</span><span class="tile">A</span><span class="tile">Y</span><span class="tile">S</span><span class="tile">I</span><span class="tile">A</span><span class="tile">-</span><span class="tile">2</span><span class="tile">0</span><span class="tile">0</span><span class="tile">6</span>
      <svg class="flag" viewBox="0 0 28 14" preserveAspectRatio="none" role="img" aria-label="Malaysia flag"><rect width="28" height="14" fill="#fff"/><g fill="#cc0001"><rect y="0" width="28" height="1"/><rect y="2" width="28" height="1"/><rect y="4" width="28" height="1"/><rect y="6" width="28" height="1"/><rect y="8" width="28" height="1"/><rect y="10" width="28" height="1"/><rect y="12" width="28" height="1"/></g><rect width="14" height="8" fill="#010066"/><circle cx="5.5" cy="4" r="2.8" fill="#fc0"/><circle cx="6.3" cy="4" r="2.3" fill="#010066"/><circle cx="10" cy="4" r="1.4" fill="#fc0"/></svg></div>

    <div class="row"><span class="tile">T</span><span class="tile">H</span><span class="tile">A</span><span class="tile">I</span><span class="tile">L</span><span class="tile">A</span><span class="tile">N</span><span class="tile">D</span><span class="tile">-</span><span class="tile">2</span><span class="tile">0</span><span class="tile">0</span><span class="tile">7</span>
      <svg class="flag" viewBox="0 0 9 6" preserveAspectRatio="none" role="img" aria-label="Thailand flag"><rect width="9" height="6" fill="#a51931"/><rect y="1" width="9" height="4" fill="#f4f5f8"/><rect y="2" width="9" height="2" fill="#2d2a4a"/></svg></div>

    <div class="row"><span class="tile">I</span><span class="tile">T</span><span class="tile">A</span><span class="tile">L</span><span class="tile">Y</span><span class="tile">-</span><span class="tile">2</span><span class="tile">0</span><span class="tile">0</span><span class="tile">9</span>
      <svg class="flag" viewBox="0 0 3 2" preserveAspectRatio="none" role="img" aria-label="Italy flag"><rect width="1" height="2" fill="#009246"/><rect x="1" width="1" height="2" fill="#fff"/><rect x="2" width="1" height="2" fill="#ce2b37"/></svg></div>

    <div class="row"><span class="tile">I</span><span class="tile">N</span><span class="tile">D</span><span class="tile">I</span><span class="tile">A</span><span class="tile">,</span><span class="tile">V</span><span class="tile">I</span><span class="tile">E</span><span class="tile">T</span><span class="tile">N</span><span class="tile">A</span><span class="tile">M</span>
      <svg class="flag" viewBox="0 0 30 15" preserveAspectRatio="none" role="img" aria-label="India flag"><rect width="30" height="5" fill="#ff9933"/><rect y="5" width="30" height="5" fill="#fff"/><rect y="10" width="30" height="5" fill="#138808"/><circle cx="15" cy="7.5" r="2" fill="none" stroke="#000080" stroke-width=".5"/></svg>
      <svg class="flag" viewBox="0 0 30 15" preserveAspectRatio="none" role="img" aria-label="Vietnam flag"><rect width="30" height="15" fill="#da251d"/><polygon fill="#ff0" points="15,2.5 16.3,6.3 20.2,6.3 17.1,8.6 18.2,12.4 15,10.1 11.8,12.4 12.9,8.6 9.8,6.3 13.7,6.3"/></svg></div>

    <div class="row"><span class="tile accent">&amp;</span><span class="tile">H</span><span class="tile">O</span><span class="tile">N</span><span class="tile">G</span><span class="tile">K</span><span class="tile">O</span><span class="tile">N</span><span class="tile">G</span><span class="tile">2</span><span class="tile">0</span><span class="tile">1</span><span class="tile">0</span>
      <svg class="flag" viewBox="0 0 3 2" preserveAspectRatio="none" role="img" aria-label="Hong Kong flag with white flower emblem"><rect width="3" height="2" fill="#de2910"/></svg></div>

    <div class="row"><span class="tile">B</span><span class="tile">A</span><span class="tile">L</span><span class="tile">I</span><span class="tile">-</span><span class="tile">2</span><span class="tile">0</span><span class="tile">1</span><span class="tile">3</span>
      <svg class="flag" viewBox="0 0 3 2" preserveAspectRatio="none" role="img" aria-label="Bali provincial flag with emblem"><rect width="3" height="2" fill="#f0a014"/></svg></div>

    <div class="row"><span class="tile">M</span><span class="tile">A</span><span class="tile">L</span><span class="tile">A</span><span class="tile">Y</span><span class="tile">S</span><span class="tile">I</span><span class="tile">A</span><span class="tile">-</span><span class="tile">2</span><span class="tile">0</span><span class="tile">1</span><span class="tile">2</span>
      <svg class="flag" viewBox="0 0 28 14" preserveAspectRatio="none" role="img" aria-label="Malaysia flag"><rect width="28" height="14" fill="#fff"/><g fill="#cc0001"><rect y="0" width="28" height="1"/><rect y="2" width="28" height="1"/><rect y="4" width="28" height="1"/><rect y="6" width="28" height="1"/><rect y="8" width="28" height="1"/><rect y="10" width="28" height="1"/><rect y="12" width="28" height="1"/></g><rect width="14" height="8" fill="#010066"/><circle cx="5.5" cy="4" r="2.8" fill="#fc0"/><circle cx="6.3" cy="4" r="2.3" fill="#010066"/><circle cx="10" cy="4" r="1.4" fill="#fc0"/></svg></div>

    <div class="row"><span class="tile">S</span><span class="tile">I</span><span class="tile">N</span><span class="tile">G</span><span class="tile">A</span><span class="tile">P</span><span class="tile">O</span><span class="tile">R</span><span class="tile">E</span><span class="tile">2</span><span class="tile">0</span><span class="tile">1</span><span class="tile">2</span>
      <svg class="flag" viewBox="0 0 30 20" preserveAspectRatio="none" role="img" aria-label="Singapore flag"><rect width="30" height="10" fill="#ef3340"/><rect y="10" width="30" height="10" fill="#fff"/><circle cx="6" cy="5" r="3.2" fill="#fff"/><circle cx="7.3" cy="5" r="3" fill="#ef3340"/><g fill="#fff"><circle cx="10" cy="3" r=".6"/><circle cx="12" cy="4.2" r=".6"/><circle cx="11.3" cy="6.5" r=".6"/><circle cx="8.8" cy="6.5" r=".6"/><circle cx="8.1" cy="4.2" r=".6"/></g></svg></div>

    <div class="row"><span class="tile">V</span><span class="tile">I</span><span class="tile">E</span><span class="tile">T</span><span class="tile">N</span><span class="tile">A</span><span class="tile">M</span><span class="tile">,</span><span class="tile">L</span><span class="tile">A</span><span class="tile">O</span><span class="tile">S</span><span class="tile accent">&amp;</span>
      <svg class="flag" viewBox="0 0 30 15" preserveAspectRatio="none" role="img" aria-label="Vietnam flag"><rect width="30" height="15" fill="#da251d"/><polygon fill="#ff0" points="15,2.5 16.3,6.3 20.2,6.3 17.1,8.6 18.2,12.4 15,10.1 11.8,12.4 12.9,8.6 9.8,6.3 13.7,6.3"/></svg>
      <svg class="flag" viewBox="0 0 30 20" preserveAspectRatio="none" role="img" aria-label="Laos flag"><rect width="30" height="20" fill="#ce1126"/><rect y="5" width="30" height="10" fill="#002868"/><circle cx="15" cy="10" r="4" fill="#fff"/></svg></div>

    <div class="row"><span class="tile">C</span><span class="tile">A</span><span class="tile">M</span><span class="tile">B</span><span class="tile">O</span><span class="tile">D</span><span class="tile">I</span><span class="tile">A</span><span class="tile">-</span><span class="tile">2</span><span class="tile">0</span><span class="tile">1</span><span class="tile">3</span>
      <svg class="flag" viewBox="0 0 30 20" preserveAspectRatio="none" role="img" aria-label="Cambodia flag with temple emblem"><rect width="30" height="20" fill="#032ea1"/><rect y="5" width="30" height="10" fill="#e00025"/></svg></div>

    <div class="row"><span class="tile">E</span><span class="tile">U</span><span class="tile">R</span><span class="tile">O</span><span class="tile">P</span><span class="tile">E</span><span class="tile">-</span><span class="tile">2</span><span class="tile">0</span><span class="tile">1</span><span class="tile">5</span>
      <svg class="flag" viewBox="0 0 30 20" preserveAspectRatio="none" role="img" aria-label="European Union flag"><rect width="30" height="20" fill="#003399"/><g fill="#fc0"><circle cx="15" cy="4" r=".8"/><circle cx="18" cy="4.8" r=".8"/><circle cx="20.2" cy="7" r=".8"/><circle cx="21" cy="10" r=".8"/><circle cx="20.2" cy="13" r=".8"/><circle cx="18" cy="15.2" r=".8"/><circle cx="15" cy="16" r=".8"/><circle cx="12" cy="15.2" r=".8"/><circle cx="9.8" cy="13" r=".8"/><circle cx="9" cy="10" r=".8"/><circle cx="9.8" cy="7" r=".8"/><circle cx="12" cy="4.8" r=".8"/></g></svg></div>
  </section>

  <p class="quote">The world is a book and<br>those who do not travel read<br><strong>only one page.</strong></p>
</main>
</body>
</html>
```